Fern Moss Cleaning Tablets needs 4 x labels

We're about to launch a very exciting cleaning product to market and need your help to brand the 4 x bottles. www.fernmossly.com.au will change the way people buy and use household cleaning products whilst significantly reducing the impact on the earth.

The tablets are dropped into the long life recycled plastic bottle, you simply add water, wait for the tab to dissolve and begin cleaning.

Target Market(s)

Women aged between 30 - 65, care for the environment, want to use less plastic, are early adopters and like to try new things. Care about a clean home and using less chemicals. Want less packaging, less plastic, less carbon emissions.

Industry/Entity Type

House Cleaning

Font styles to use
Sans Serif

Requirements
Must have
• Each label must have an obvious colour differentiator and each label must be identical in it's dimensions and information. Should look uniform when all 4 bottles are aligned in the cupboard. Limited / no images apart from logo.
Nice to have
• Simple, clear, bold, striking. Limited / no pictures. Clean lines with lots of space.
Should not have
• Sparkwell Pane Label must have a strip of blue (hex BAE1FF).
Grime Hauler Kitchen Cleaner must have a strip of colour (FFD6F3)
The Fizzer Bathroom cleaner must have a colour strip hex # FFFFBA
The Allrounder Multip Purpose must have a strip of colour Hex #BAFFC9

```html
<!DOCTYPE html>
<html lang="en">
<head>
<meta charset="utf-8">
<title>Fern Moss – The Fizzer Bathroom Cleaner Label</title>
<link rel="stylesheet" href="https://fonts.googleapis.com/css2?family=Questrial&family=Montserrat:wght@700;800&family=Big+Shoulders+Display:wght@800&display=swap">
<style>
  :root {
    --label-top: #fdfdf1;
    --label-bottom: #f8f5c0;
    --brand-teal: #114f5e;
    --product-tan: #b8ab82;
    --ink: #000000;
    --edge: #111111;
    --page: #ffffff;
  }
  html, body {
    margin: 0;
    padding: 0;
    width: 1200px;
    height: 924px;
    overflow: hidden;
    background: var(--page);
  }
  body {
    position: relative;
  }
  .label {
    position: absolute;
    left: -2px;
    top: 3px;
    width: 1195px;
    height: 960px;
    box-sizing: border-box;
    border: 2px solid var(--edge);
    border-radius: 68px;
    background: linear-gradient(to bottom, var(--label-top), var(--label-bottom) 95%);
    overflow: hidden;
  }
  .line {
    position: absolute;
    left: 0;
    width: 1200px;
    text-align: center;
    white-space: nowrap;
    margin: 0;
    font-weight: normal;
  }
  .brand-name {
    top: 100px;
    font-family: "Montserrat", sans-serif;
    font-weight: 800;
    font-size: 88px;
    line-height: 1;
    color: var(--brand-teal);
    letter-spacing: -1px;
  }
  .product-name {
    top: 278px;
    font-family: "Questrial", sans-serif;
    font-size: 142px;
    line-height: 1;
    color: var(--product-tan);
    letter-spacing: 1px;
  }
  .product-type {
    top: 446px;
    font-family: "Big Shoulders Display", sans-serif;
    font-weight: 800;
    font-size: 156px;
    line-height: 1;
    color: var(--ink);
  }
  .product-type span {
    display: inline-block;
    transform: scaleX(0.74);
    transform-origin: center;
  }
  .tagline {
    top: 690px;
    font-family: "Questrial", sans-serif;
    font-size: 35px;
    line-height: 1;
    color: var(--ink);
    word-spacing: 4px;
  }
  .volume {
    top: 762px;
    font-family: "Montserrat", sans-serif;
    font-weight: 800;
    font-size: 40px;
    line-height: 1;
    color: var(--ink);
  }
  .origin {
    top: 846px;
    font-family: "Big Shoulders Display", sans-serif;
    font-weight: 800;
    font-size: 37px;
    line-height: 1;
    color: var(--ink);
    letter-spacing: 1px;
    word-spacing: 8px;
  }
</style>
</head>
<body>
  <main class="label">
    <p class="line brand-name">Fern Moss</p>
    <h1 class="line product-name">The Fizzer</h1>
    <h2 class="line product-type"><span>Bathroom Cleaner</span></h2>
    <p class="line tagline">One Bottle. &nbsp;One Tab. &nbsp;Dissolve. &nbsp;Clean. &nbsp;Repeat.</p>
    <p class="line volume">500 ml</p>
    <p class="line origin">Torquay. Australia</p>
  </main>
</body>
</html>
```